BUSINESS CARD - HALLORAN FIELD SERVICES

I would like to create a business card for my fertilizer spreading business. I would like to incorporate my existing logo and also a description of the services offered. The business card will be given to farmers so must be kept simple but effective. It will also be left in stores so much also be eye catching in order to stand out from other cards.

Target Market(s)

FARMERS

Requirements
Must have
• FRONT OF CARD = EXISTING LOGO + "CUSTOMISED SPREADING" below the logo

REAR Of CARD = SERVICES OFFERED AND CONTACT DETAILS

- Bulk fertilizer including Lime, Gypsum, Manure & Compost
- Granular fertilizer including Single Super, Urea, Gran-am, & Custom Blends
- Modern equipment - Autosteer & Variable Rate Capable
- Friendly & Reliable Service
- Contact Gus: 0417 552 308
Nice to have
• utilize same color scheme as existing logo

```html
<!DOCTYPE html>
<html lang="en">
<head>
<meta charset="utf-8">
<title>Halloran Field Services – Business Card</title>
<link rel="stylesheet" href="https://fonts.googleapis.com/css2?family=Open+Sans:wght@400;600&display=swap">
<style>
  :root {
    --backdrop: #3b4046;
    --card-white: #ffffff;
    --card-black: #0b0b0c;
    --ink: #3d3d3d;
    --ink-soft: #555555;
    --accent: #f08a12;
    --logo-grey: #8e8e8e;
    --pattern-tone: #161617;
  }
  * { box-sizing: border-box; margin: 0; padding: 0; }
  html, body {
    width: 1200px; height: 900px; overflow: hidden;
    background: var(--backdrop);
    font-family: "Open Sans", Arial, sans-serif;
  }
  .stage {
    width: 1200px; height: 900px;
    display: flex; align-items: center; justify-content: center; gap: 40px;
  }
  .card {
    position: relative;
    width: 540px; height: 310px;
    border-radius: 14px;
    overflow: hidden;
  }

  /* Rear: services + contact */
  .card-rear { background: var(--card-white); color: var(--ink); }
  .card-rear .emblem-ghost {
    position: absolute; left: 150px; top: 80px;
    width: 190px; height: 190px; border-radius: 50%;
    background: radial-gradient(circle, rgba(0,0,0,0.045) 0%, rgba(0,0,0,0.02) 60%, rgba(0,0,0,0) 72%);
  }
  .contact-name {
    position: absolute; left: 30px; top: 26px;
    font-size: 21px; font-weight: 600; color: var(--ink);
  }
  .contact-role {
    position: absolute; left: 30px; top: 56px;
    font-size: 15px; color: var(--accent);
  }
  .services {
    position: absolute; left: 30px; top: 118px;
    list-style: none;
    font-size: 14.5px; line-height: 1.5; color: var(--ink-soft);
  }
  .services li { position: relative; padding-left: 18px; }
  .services li::before {
    content: ""; position: absolute; left: 0; top: 6px;
    width: 11px; height: 11px; border-radius: 50%;
    background: var(--accent);
  }
  .phone {
    position: absolute; right: 32px; bottom: 28px;
    display: flex; align-items: center; gap: 8px;
    font-size: 19px; letter-spacing: 1px; color: var(--ink);
  }
  .phone svg { width: 18px; height: 18px; fill: var(--accent); }

  /* Front: brand */
  .card-front { background: var(--card-black); }
  .card-front .pattern-field {
    position: absolute; inset: 0;
    background: linear-gradient(135deg, var(--pattern-tone), var(--card-black));
  }
  .brand {
    position: absolute; right: 30px; bottom: 52px;
    display: flex; flex-direction: column; align-items: flex-end; gap: 8px;
  }
  .brand-row { display: flex; align-items: center; gap: 14px; }
  .brand-dot {
    width: 44px; height: 44px; border-radius: 50%;
    background: var(--logo-grey);
  }
  .brand-name {
    font-size: 25px; font-weight: 600; letter-spacing: 0.5px;
    color: var(--logo-grey);
  }
  .tagline {
    display: flex; align-items: center; gap: 10px;
    width: 100%;
  }
  .tagline-rule {
    flex: 1; height: 2px; background: var(--accent);
  }
  .tagline-text {
    font-size: 14px; font-weight: 600; letter-spacing: 3px;
    color: var(--accent); white-space: nowrap;
  }
</style>
</head>
<body>
  <main class="stage">
    <section class="card card-rear" aria-label="Card rear">
      <div class="emblem-ghost" role="img" aria-label="Faint company emblem in the background"></div>
      <h1 class="contact-name">Gus</h1>
      <p class="contact-role">ceo / General Manager</p>
      <ul class="services">
        <li>Bulk fertilizer including Lime, Gypsum, Manure &amp; Compost.</li>
        <li>Granular fertilizer including Single Super,<br>Urea, Gran-am, &amp; Custom Blends.</li>
        <li>Modern equipment - Autosteer &amp; Variable Rate Capable.</li>
        <li>Friendly &amp; Reliable Service.</li>
      </ul>
      <p class="phone">
        <svg viewBox="0 0 24 24" aria-hidden="true"><path d="M6.6 10.8a15.1 15.1 0 0 0 6.6 6.6l2.2-2.2a1 1 0 0 1 1-.25 11.4 11.4 0 0 0 3.6.57 1 1 0 0 1 1 1V20a1 1 0 0 1-1 1A17 17 0 0 1 3 4a1 1 0 0 1 1-1h3.5a1 1 0 0 1 1 1c0 1.25.2 2.45.57 3.57a1 1 0 0 1-.25 1z"/></svg>
        0417 552 308
      </p>
    </section>

    <section class="card card-front" aria-label="Card front">
      <div class="pattern-field" role="img" aria-label="Dark repeating emblem pattern across the card"></div>
      <div class="brand">
        <div class="brand-row">
          <span class="brand-dot" aria-hidden="true"></span>
          <span class="brand-name">HALLORAN FIELD SERVICES</span>
        </div>
        <div class="tagline">
          <span class="tagline-rule" aria-hidden="true"></span>
          <span class="tagline-text">CUSTOMISED SPREADING</span>
          <span class="tagline-rule" aria-hidden="true"></span>
        </div>
      </div>
    </section>
  </main>
</body>
</html>
```